Website for Swedish wellness company "Heartmeadow"

We need a website for our Swedish wellness company. The name is "Heartmeadow" . The company is all about sustainablility for our body, soul and planet. We work with coaching, yoga, massage, healthy food, retreats(sports, excercise, sufing), healing and inspirational talks. We are convinced that personal sustainability and a strong spiritual connection to yourself will lead to planetary sustainability. Our customers are both companies and consumers from all over the world. The final design should be clean/simple and you should get a feeling of community, happiness, warmth, connection,, joy, spirituality but still a professional touch.Just got a logo from Pixel Harbor and are very happy with it;-)
Updates

Sorry I was too enthusiastic posting this project. Of course I will give you some text as well för the different pages! I will see to that it is finished by friday so if you want to wait with your submissions please do! Best regards Maria

Target Market(s)

Businesses and consumers

Industry/Entity Type

Health And Wellness

Number of Pages Required

5+ page

Font styles to use
Sans Serif

Colors
33a6d7
00a990
b7a5cd

Requirements
Must have
• Idea about pages:
• I am not sure how many pages I get for the price, but 5 would be nice to start with.
• Not sure what write ups is;-)
• But title of the pages could be:
• Landing page
• About us
• Services
• Retreats
• Contact us
Nice to have
• A clean and professional website but with some heart and soul in it. Because we Would love colours that harmonize with our logo, but other ideas are welcome!

```html
<!DOCTYPE html>
<html lang="en">
<head>
<meta charset="utf-8">
<title>Heartmeadow – Body, Soul and Planet</title>
<link rel="stylesheet" href="https://fonts.googleapis.com/css2?family=Poppins:wght@400;500;600&family=Lato:wght@400;700&display=swap">
<style>
:root{
  --green:#00a990;
  --teal:#4fc1bf;
  --teal-dark:#1f8f7e;
  --purple:#9b86c4;
  --purple-soft:#b7a5cd;
  --navy:#132a57;
  --ink:#1c1c1c;
  --text:#5d5d5d;
  --mist:#e8f1f4;
  --line:#d8d8d8;
  --white:#ffffff;
}
*{box-sizing:border-box;margin:0;padding:0}
html,body{width:1200px;height:3919px;overflow:hidden;background:var(--white)}
body{position:relative;font-family:"Poppins",sans-serif;color:var(--ink)}
.abs{position:absolute}
h2.section-title{position:absolute;left:0;width:1200px;text-align:center;font-weight:500;font-size:42px;letter-spacing:1px;color:var(--ink)}

/* header */
.site-header{position:absolute;top:0;left:0;width:1200px;height:100px;background:var(--white);z-index:3}
.brand-disc{position:absolute;left:84px;top:-56px;width:266px;height:266px;border-radius:50%;background:var(--white);z-index:4}
.brand-name{position:absolute;left:84px;top:112px;width:266px;text-align:center;font-family:"Poppins",sans-serif;font-weight:500;font-size:28px;color:var(--navy);letter-spacing:.5px;z-index:5}
.brand-dot{position:absolute;left:193px;top:22px;width:48px;height:48px;border-radius:50%;border:6px solid var(--teal);z-index:5}
.topline{position:absolute;right:111px;top:18px;font-size:17px;color:var(--ink);display:flex;gap:14px;align-items:center}
.topline svg{vertical-align:-2px;margin-right:6px}
.main-nav{position:absolute;right:111px;top:61px;display:flex;gap:31px;font-size:17px;font-weight:500;align-items:center}
.main-nav a{color:var(--ink);text-decoration:none}
.main-nav a.active{color:var(--green)}

/* hero */
.hero{position:absolute;top:100px;left:0;width:1200px;height:624px;background:linear-gradient(180deg,#3b7fc4 0%,#6ea7cf 30%,#4b7288 55%,#b8c8d4 72%,#dfe6ea 85%,#8a7a68 100%)}
.hero-title{position:absolute;top:90px;width:1200px;text-align:center;color:var(--white);font-weight:600;font-size:72px;letter-spacing:2px}
.hero-sub{position:absolute;top:188px;width:1200px;text-align:center;color:var(--white);font-family:"Lato",sans-serif;font-size:27px}
.hero-btn{position:absolute;left:505px;top:254px;width:190px;height:55px;border:2px solid var(--white);border-radius:28px;color:var(--white);font-weight:600;font-size:16px;letter-spacing:.5px;display:flex;align-items:center;justify-content:center}
.hero-dots{position:absolute;top:556px;left:563px;display:flex;gap:7px}
.hero-dots span{width:13px;height:13px;border-radius:50%;border:2px solid var(--white)}
.hero-dots span.on{background:var(--white)}

/* welcome */
.welcome h2{position:absolute;left:112px;top:820px;font-size:42px;font-weight:500;letter-spacing:1px}
.welcome p{position:absolute;left:112px;top:900px;width:570px;font-size:14.5px;line-height:29px;color:var(--text)}
.btn-outline{position:absolute;border:2px solid var(--purple-soft);border-radius:26px;color:var(--purple);font-weight:600;font-size:16px;display:flex;align-items:center;justify-content:center}
.welcome-photo{position:absolute;left:740px;top:808px;width:346px;height:346px}

/* services */
.services{position:absolute;top:1226px;left:0;width:1200px;height:722px;background:var(--mist)}
.svc{position:absolute;width:320px}
.svc h3{font-size:22px;font-weight:500;color:var(--ink)}
.svc p{font-family:"Lato",sans-serif;font-size:15px;color:var(--text);margin-top:10px}
.svc.left{text-align:right}
.svc-icon{position:absolute;width:90px;height:90px;border-radius:50%;background:var(--white);box-shadow:0 3px 10px rgba(0,0,0,.1);display:flex;align-items:center;justify-content:center}

/* blog */
.post{position:absolute;top:2140px;width:308px}
.post-img{width:308px;height:222px}
.post h3{margin-top:36px;font-size:21px;font-weight:500}
.post .meta{margin-top:12px;font-family:"Lato",sans-serif;font-size:14px;color:var(--ink);display:flex;gap:8px;align-items:center}
.post .meta svg{margin-right:2px}
.post p{margin-top:20px;font-family:"Lato",sans-serif;font-size:14px;line-height:27px;color:var(--text)}
.post .more{margin-top:22px;font-weight:600;font-size:15px;color:var(--purple)}

/* testimonials */
.wave{position:absolute;top:2540px;left:0;width:1200px;height:620px}
.testi-title{position:absolute;top:2815px;width:1200px;text-align:center;color:var(--white);font-weight:500;font-size:42px;letter-spacing:1px}
.quote-card{position:absolute;top:2948px;width:307px;height:258px;background:var(--white);box-shadow:0 2px 10px rgba(0,0,0,.15);text-align:center;padding:66px 24px 0}
.quote-card p{font-family:"Lato",sans-serif;font-style:italic;font-size:14px;line-height:25px;color:var(--text)}
.quote-card h4{margin-top:16px;font-size:18px;font-weight:500}
.quote-card .role{margin-top:6px;font-family:"Lato",sans-serif;font-style:italic;font-size:14px;color:var(--purple)}
.avatar{position:absolute;top:-42px;left:111px;width:84px;height:84px;border-radius:50%;background:linear-gradient(180deg,#d9cbbd,#b59a82);border:3px solid var(--white)}
.next-btn{position:absolute;left:1131px;top:3025px;width:44px;height:44px;border-radius:50%;border:2px solid var(--white)}

/* contact */
.sub-title{position:absolute;font-size:22px;font-weight:500}
.field{position:absolute;border:1px solid #9a9a9a;border-radius:8px;font-family:"Lato",sans-serif;font-size:14px;color:var(--text);padding:14px 15px}
.submit{position:absolute;left:617px;top:3719px;width:96px;height:40px;border-radius:20px;background:var(--purple-soft);color:var(--white);font-weight:600;font-size:14px;display:flex;align-items:center;justify-content:center}
.info-row{position:absolute;left:779px;display:flex;gap:16px;align-items:flex-start;font-family:"Lato",sans-serif;font-size:14px;line-height:24px;color:var(--ink)}
.info-ic{width:33px;height:33px;border-radius:50%;border:1px solid #bbb;display:flex;align-items:center;justify-content:center;flex:none}
.social{position:absolute;top:3739px;left:776px;display:flex;gap:11px}
.social span{width:35px;height:35px;border-radius:50%;border:2px solid var(--purple-soft)}
.footer-line{position:absolute;top:3813px;left:111px;width:970px;border-top:1px solid var(--line)}
.copyright{position:absolute;top:3853px;width:1200px;text-align:center;font-family:"Lato",sans-serif;font-size:14px;color:var(--ink)}
</style>
</head>
<body>

<header class="site-header">
  <div class="topline">
    <span><svg width="13" height="13" viewBox="0 0 24 24"><path fill="#00a990" d="M6.6 10.8a15 15 0 0 0 6.6 6.6l2.2-2.2c.3-.3.7-.4 1-.2 1.1.4 2.3.6 3.6.6.6 0 1 .4 1 1V20c0 .6-.4 1-1 1A17 17 0 0 1 3 4c0-.6.4-1 1-1h3.5c.6 0 1 .4 1 1 0 1.3.2 2.5.6 3.6.1.3 0 .7-.2 1z"/></svg>1 555 010 2040</span>
    <span>|</span>
    <span><svg width="15" height="12" viewBox="0 0 24 18"><rect width="24" height="18" rx="2" fill="#00a990"/><path d="M1 1l11 9 11-9" stroke="#fff" stroke-width="2" fill="none"/></svg>info@heartmeadow.se</span>
  </div>
  <nav class="main-nav">
    <a class="active" href="#">Home</a>
    <a href="#">About us</a>
    <a href="#">Services</a>
    <a href="#">Retreats</a>
    <a href="#">Contact us</a>
    <svg width="17" height="17" viewBox="0 0 24 24"><circle cx="10" cy="10" r="7" stroke="#1c1c1c" stroke-width="3" fill="none"/><path d="M15 15l6 6" stroke="#1c1c1c" stroke-width="3.5" stroke-linecap="round"/></svg>
  </nav>
</header>

<section class="hero" role="img" aria-label="Woman meditating cross-legged on a tree stump above clouds and mountains">
  <div class="hero-title">HEARTMEADOW</div>
  <div class="hero-sub">We are all about sustainablility for our body, soul and planet.</div>
  <div class="hero-btn">GET MORE INFO</div>
  <div class="hero-dots"><span class="on"></span><span></span><span></span><span></span></div>
</section>

<div class="brand-disc"></div>
<div class="brand-dot"></div>
<div class="brand-name">HEARTMEADOW</div>

<section class="welcome">
  <h2>WELCOME TO HEARTMEADOW</h2>
  <p>Nam libero tempore, cum soluta nobis est eligendi optio cumque nihil impminus id quod maxime placeat facere possimus, omnis voluptas assumenda mnis dolorr ep ellendus. Temporibus autem quibusdam et aut officiis debitis aut rerum necessitat ib us saepe eveniet ut et voluptates repudiandae.</p>
  <div class="btn-outline" style="left:113px;top:1057px;width:153px;height:50px">READ MORE</div>
  <svg class="welcome-photo" viewBox="0 0 346 346">
    <defs><radialGradient id="softbg"><stop offset="0" stop-color="#f4f4f4"/><stop offset="1" stop-color="#dcdcdc"/></radialGradient></defs>
    <path d="M136 6 A170 170 0 0 0 136 340" stroke="#4fc1bf" stroke-width="22" fill="none"/>
    <path d="M210 6 A170 170 0 0 1 210 340" stroke="#4fc1bf" stroke-width="22" fill="none"/>
    <circle cx="173" cy="173" r="146" fill="url(#softbg)" role="img" aria-label="Woman in a standing forward-bend yoga pose"/>
  </svg>
</section>

<section class="services">
  <h2 class="section-title" style="top:80px">WHAT WE DO</h2>

  <div class="svc left" style="left:27px;top:191px"><h3>Coaching</h3><p>At vero eos et accusamus etust</p></div>
  <div class="svc left" style="left:27px;top:302px"><h3>yoga</h3><p>At vero eos et accusamus etust</p></div>
  <div class="svc left" style="left:27px;top:413px"><h3>Massage</h3><p>At vero eos et accusamus etust</p></div>
  <div class="svc" style="left:865px;top:191px"><h3>Healthy Food</h3><p>At vero eos et accusamus etust</p></div>
  <div class="svc" style="left:865px;top:302px"><h3>Retreats</h3><p>At vero eos et accusamus etust</p></div>
  <div class="svc" style="left:865px;top:413px"><h3>Healing</h3><p>At vero eos et accusamus etust</p></div>
  <div class="svc" style="left:440px;top:576px;text-align:center"><h3>Inspirational Talks</h3><p>At vero eos et accusamus etust</p></div>

  <div class="svc-icon" style="left:369px;top:174px"><svg width="42" height="36" viewBox="0 0 42 36"><path d="M4 4h24v16H14l-6 5v-5H4z" fill="none" stroke="#9b86c4" stroke-width="3" stroke-linejoin="round"/><path d="M32 12h6v14h-4v5l-6-5H16v-3" fill="none" stroke="#9b86c4" stroke-width="3" stroke-linejoin="round"/></svg></div>
  <div class="svc-icon" style="left:369px;top:285px"><svg width="40" height="40" viewBox="0 0 40 40"><circle cx="20" cy="7" r="5" fill="#9b86c4"/><path d="M20 14v12M8 22l12-6 12 6M6 32h28" stroke="#9b86c4" stroke-width="4" stroke-linecap="round" fill="none"/></svg></div>
  <div class="svc-icon" style="left:369px;top:396px"><svg width="40" height="40" viewBox="0 0 40 40"><rect x="6" y="16" width="10" height="20" rx="2" fill="#9b86c4"/><path d="M11 6c3 4 3 6 0 8-3-2-3-4 0-8z" fill="#9b86c4"/><path d="M18 36c0-14 8-20 18-22-2 12-8 20-18 22z" fill="#9b86c4"/></svg></div>
  <div class="svc-icon" style="left:741px;top:174px"><svg width="36" height="38" viewBox="0 0 36 38"><path d="M18 12c-6-4-14-2-14 8s6 16 10 16c2 0 3-1 4-1s2 1 4 1c4 0 10-6 10-16s-8-12-14-8z" fill="#9b86c4"/><path d="M18 12c0-5 2-8 6-10" stroke="#9b86c4" stroke-width="3" fill="none"/></svg></div>
  <div class="svc-icon" style="left:741px;top:285px"><svg width="42" height="40" viewBox="0 0 42 40"><circle cx="28" cy="6" r="5" fill="#9b86c4"/><path d="M12 14l10-3 6 8-6 6 4 10M22 25l-8 6M28 19l8 3M2 16h8M4 22h8M2 28h6" stroke="#9b86c4" stroke-width="4" stroke-linecap="round" fill="none"/></svg></div>
  <div class="svc-icon" style="left:741px;top:396px"><svg width="40" height="40" viewBox="0 0 40 40"><circle cx="20" cy="20" r="7" fill="none" stroke="#9b86c4" stroke-width="4"/><g stroke="#9b86c4" stroke-width="4" stroke-linecap="round"><path d="M20 2v5M20 33v5M2 20h5M33 20h5M7 7l4 4M29 29l4 4M7 33l4-4M29 11l4-4"/></g></svg></div>
  <div class="svc-icon" style="left:556px;top:466px"><svg width="40" height="40" viewBox="0 0 40 40"><path d="M20 10a9 9 0 0 0-5 16v4h10v-4a9 9 0 0 0-5-16z" fill="#9b86c4"/><rect x="15" y="32" width="10" height="4" rx="2" fill="#9b86c4"/><g stroke="#9b86c4" stroke-width="3" stroke-linecap="round"><path d="M20 1v4M5 18h4M31 18h4M9 7l3 3M31 7l-3 3"/></g></svg></div>

  <svg class="abs" style="left:499px;top:205px" width="204" height="204" viewBox="0 0 204 204">
    <circle cx="102" cy="102" r="90" fill="none" stroke="#4fc1bf" stroke-width="12"/>
  </svg>
</section>

<section class="blog">
  <h2 class="section-title" style="top:2043px">LATEST BLOG</h2>

  <article class="post" style="left:111px">
    <div class="post-img" role="img" aria-label="Two people doing yoga on a sandy beach" style="background:linear-gradient(180deg,#cfd6da,#e5ddd2 55%,#c9b39a)"></div>
    <h3>Nemo enim ipsam voluptate</h3>
    <div class="meta"><svg width="13" height="13" viewBox="0 0 14 14"><rect x="1" y="2" width="12" height="11" rx="1" fill="none" stroke="#33a6d7" stroke-width="2"/><path d="M1 6h12" stroke="#33a6d7" stroke-width="2"/></svg>Fri Nov 9, 2018 <span>|</span><svg width="12" height="13" viewBox="0 0 12 13"><circle cx="6" cy="3.5" r="3" fill="#33a6d7"/><path d="M0 13a6 6 0 0 1 12 0z" fill="#33a6d7"/></svg>Erik Lund</div>
    <p>At vero eos et accusamus et iusto odio dignissi mos ducimus qui blandit cum soluta nobis este ligendi optio cumque nihil im.</p>
    <div class="more">READ MORE</div>
  </article>

  <article class="post" style="left:446px">
    <div class="post-img" role="img" aria-label="Therapist giving a leg massage" style="background:linear-gradient(135deg,#3b3a3a,#8a7a6e 50%,#5a6470)"></div>
    <h3>Nemo enim ipsam voluptate</h3>
    <div class="meta"><svg width="13" height="13" viewBox="0 0 14 14"><rect x="1" y="2" width="12" height="11" rx="1" fill="none" stroke="#33a6d7" stroke-width="2"/><path d="M1 6h12" stroke="#33a6d7" stroke-width="2"/></svg>Fri Nov 9, 2018 <span>|</span><svg width="12" height="13" viewBox="0 0 12 13"><circle cx="6" cy="3.5" r="3" fill="#33a6d7"/><path d="M0 13a6 6 0 0 1 12 0z" fill="#33a6d7"/></svg>Erik Lund</div>
    <p>At vero eos et accusamus et iusto odio dignissi mos ducimus qui blandit cum soluta nobis este ligendi optio cumque nihil im.</p>
    <div class="more">READ MORE</div>
  </article>

  <article class="post" style="left:780px">
    <div class="post-img" role="img" aria-label="Green apple, fresh salad and measuring tape on a wooden table" style="background:linear-gradient(135deg,#4a3f4a,#6c9a3c 45%,#a23a2a 70%,#3e3543)"></div>
    <h3>Nemo enim ipsam voluptate</h3>
    <div class="meta"><svg width="13" height="13" viewBox="0 0 14 14"><rect x="1" y="2" width="12" height="11" rx="1" fill="none" stroke="#33a6d7" stroke-width="2"/><path d="M1 6h12" stroke="#33a6d7" stroke-width="2"/></svg>Fri Nov 9, 2018 <span>|</span><svg width="12" height="13" viewBox="0 0 12 13"><circle cx="6" cy="3.5" r="3" fill="#33a6d7"/><path d="M0 13a6 6 0 0 1 12 0z" fill="#33a6d7"/></svg>Erik Lund</div>
    <p>At vero eos et accusamus et iusto odio dignissi mos ducimus qui blandit cum soluta nobis este ligendi optio cumque nihil im.</p>
    <div class="more">READ MORE</div>
  </article>
</section>

<section class="testimonials">
  <svg class="wave" viewBox="0 0 1200 620" preserveAspectRatio="none" role="img" aria-label="Flowing green background with soft light">
    <defs><linearGradient id="greenflow" x1="0" y1="0" x2="1" y2="0"><stop offset="0" stop-color="#1f8f7e"/><stop offset=".5" stop-color="#3db6a3"/><stop offset="1" stop-color="#0e7f6c"/></linearGradient></defs>
    <path d="M0 175 C300 250 700 240 900 160 C1050 95 1150 60 1200 20 L1200 590 C1000 560 700 520 400 470 C200 440 80 440 0 442 Z" fill="url(#greenflow)"/>
  </svg>
  <h2 class="testi-title">CLIENT TESTIMONIALS</h2>

  <div class="quote-card" style="left:99px">
    <div class="avatar" role="img" aria-label="Client portrait"></div>
    <p>“ Nam libero tempore, cum soluta nobis est eligendi optio cumque nihil impedit quo minus id quod maxime placeat facere possi mus, omqumnis volup”</p>
    <h4>Oskar Berglin</h4>
    <div class="role">Propriétaire - Berglin Studio</div>
  </div>
  <div class="quote-card" style="left:446px">
    <div class="avatar" role="img" aria-label="Client portrait"></div>
    <p>“ Nam libero tempore, cum soluta nobis est eligendi optio cumque nihil impedit quo minus id quod maxime placeat facere possi mus, omqumnis volup”</p>
    <h4>Lena Holmvik</h4>
    <div class="role">Propriétaire - Fjord Travels</div>
  </div>
  <div class="quote-card" style="left:794px">
    <div class="avatar" role="img" aria-label="Client portrait"></div>
    <p>“ Nam libero tempore, cum soluta nobis est eligendi optio cumque nihil impedit quo minus id quod maxime placeat facere possi mus, omqumnis volup”</p>
    <h4>Nils Ekdahl</h4>
    <div class="role">Propriétaire - Ljus Atelier</div>
  </div>
  <div class="next-btn"><svg width="40" height="40" viewBox="0 0 40 40"><path d="M17 12l8 8-8 8" stroke="#fff" stroke-width="2.5" fill="none" stroke-linecap="round"/></svg></div>
</section>

<section class="contact">
  <h2 class="section-title" style="top:3318px">CONTACT US</h2>

  <div class="sub-title" style="left:110px;top:3432px">Contact form</div>
  <div class="field" style="left:111px;top:3494px;width:297px;height:44px">Name :</div>
  <div class="field" style="left:417px;top:3494px;width:296px;height:44px">Phone no :</div>
  <div class="field" style="left:111px;top:3555px;width:602px;height:44px">Email :</div>
  <div class="field" style="left:111px;top:3616px;width:602px;height:82px">Message :</div>
  <div class="submit">SUBMIT</div>

  <div class="sub-title" style="left:778px;top:3432px">Contact Information</div>
  <div class="info-row" style="top:3490px">
    <span class="info-ic"><svg width="12" height="16" viewBox="0 0 12 16"><path d="M6 0a6 6 0 0 0-6 6c0 4 6 10 6 10s6-6 6-10a6 6 0 0 0-6-6z" fill="#33a6d7"/><circle cx="6" cy="6" r="2.2" fill="#fff"/></svg></span>
    <span>41 Lindgatan, Suite 12<br>Uppsala, Sweden 75320</span>
  </div>
  <div class="info-row" style="top:3553px">
    <span class="info-ic"><svg width="14" height="14" viewBox="0 0 24 24"><path fill="#33a6d7" d="M6.6 10.8a15 15 0 0 0 6.6 6.6l2.2-2.2c.3-.3.7-.4 1-.2 1.1.4 2.3.6 3.6.6.6 0 1 .4 1 1V20c0 .6-.4 1-1 1A17 17 0 0 1 3 4c0-.6.4-1 1-1h3.5c.6 0 1 .4 1 1 0 1.3.2 2.5.6 3.6.1.3 0 .7-.2 1z"/></svg></span>
    <span style="line-height:33px">1 555 010 2040</span>
  </div>
  <div class="info-row" style="top:3614px">
    <span class="info-ic"><svg width="15" height="11" viewBox="0 0 24 18"><rect width="24" height="18" rx="2" fill="#33a6d7"/><path d="M1 1l11 9 11-9" stroke="#fff" stroke-width="2" fill="none"/></svg></span>
    <span style="line-height:33px">info@heartmeadow.se</span>
  </div>

  <div class="sub-title" style="left:778px;top:3690px">Social Media</div>
  <div class="social"><span></span><span></span><span></span></div>
</section>

<footer>
  <div class="footer-line"></div>
  <div class="copyright">Copyright © 2019, Heartmeadow All rights reserved.</div>
  <svg class="abs" style="left:1061px;top:3845px" width="28" height="18" viewBox="0 0 28 18"><path d="M2 15L14 4l12 11" stroke="#aaa" stroke-width="2.5" fill="none"/></svg>
</footer>

</body>
</html>
```